IT Freelancer (Consulting, trainer and project manager) needed letterhead

As a freelancer for IT Trainingswhip, consulting and project management I need a letterhead design. What is desired is a design that fits the existing logo (see Annex). It is functional, reliable, and equal time wirkenn Agil and modern. The whole is in color, as well as printed out to make a good impression on a black and white printer. The whole is to the existing Cooperate design (business card, homepage, logo) fit. Therefore, the choice of colors.
Updates

Target Market(s)

Customers such as medium-sized enterprises, training institutions

Industry/Entity Type

Consulting

Colors
0455a3
3277b5
85abd2
cfdfed
34a6d7
32a6d6
249fd4
0792cd
85cae6

Requirements
Must have
• Must include logo (see Annex) address (Brunnerweg 14, 37281 Eichenfeld, Germany). Must seriously and act simultaneously Agil. Design should (even) be adaptable (signature, address, etc.) design must look good on a black / white laser

```html
<!DOCTYPE html>
<html lang="en">
<head>
<meta charset="utf-8">
<title>Lorenz Keller – Letterhead</title>
<link rel="stylesheet" href="https://fonts.googleapis.com/css2?family=Lato:wght@400;700;900&display=swap">
<style>
  :root {
    --navy: #0455a3;
    --blue: #3277b5;
    --sky: #34a6d7;
    --light: #85cae6;
    --pale: #cfdfed;
    --ink: #333a44;
    --backdrop: #e9eaec;
    --paper: #ffffff;
  }
  * { margin: 0; padding: 0; box-sizing: border-box; }
  html, body {
    width: 1200px; height: 794px; overflow: hidden;
    background: var(--backdrop);
    font-family: "Lato", Arial, sans-serif;
  }
  .canvas { position: relative; width: 1200px; height: 794px; }
  .letterhead {
    position: absolute; left: 333px; top: 20px;
    width: 533px; height: 754px;
    background: var(--paper);
    box-shadow: 0 2px 10px rgba(0,0,0,.08);
    overflow: hidden;
  }
  .side-band {
    position: absolute; top: 0; right: 0; width: 14px; height: 100%;
    background: var(--navy);
  }
  .side-band__accent { position: absolute; left: 0; width: 100%; }
  .side-band__accent--blue  { top: 34px; height: 18px; background: var(--blue); }
  .side-band__accent--sky   { top: 56px; height: 18px; background: var(--sky); }
  .side-band__accent--light { top: 78px; height: 10px; background: var(--light); }
  .side-band__gap { position: absolute; left: 0; width: 100%; height: 4px; background: var(--paper); }
  .side-band__gap--1 { top: 30px; }
  .side-band__gap--2 { top: 52px; }
  .side-band__gap--3 { top: 74px; }
  .side-band__gap--4 { top: 88px; }
  .web-address {
    position: absolute; right: 0; bottom: 14px; width: 14px; height: 120px;
    writing-mode: vertical-rl; transform: rotate(180deg);
    display: flex; align-items: center; justify-content: flex-start;
    color: var(--paper); font-size: 8px; letter-spacing: .3px; white-space: nowrap;
  }
  .circuit-corner {
    position: absolute; left: 0; top: 0; width: 150px; height: 115px;
    background: linear-gradient(150deg, var(--pale) 0%, rgba(133,202,230,.5) 50%, rgba(255,255,255,0) 100%);
  }
  .brand {
    position: absolute; top: 32px; right: 34px;
    display: flex; align-items: center; gap: 8px;
  }
  .brand__dot { width: 34px; height: 34px; border-radius: 50%; background: var(--navy); }
  .brand__name {
    font-weight: 900; font-size: 15px; line-height: 1.05; color: var(--navy);
    text-transform: uppercase; letter-spacing: .5px;
  }
  .brand__divider {
    position: absolute; top: 30px; right: 168px; width: 1px; height: 70px;
    background: var(--pale);
  }
  .contact {
    position: absolute; top: 48px; right: 180px;
    font-style: normal; font-size: 7.5px; line-height: 1.35; color: var(--ink);
  }
  .contact__row { display: flex; align-items: center; gap: 4px; }
  .contact__row svg { width: 7px; height: 7px; fill: var(--navy); }
  .sender-line {
    position: absolute; left: 62px; top: 122px;
    font-size: 6px; color: var(--ink); letter-spacing: .1px;
  }
</style>
</head>
<body>
<div class="canvas">
  <article class="letterhead">
    <div class="circuit-corner" role="img" aria-label="Light blue circuit-board trace pattern"></div>

    <div class="side-band">
      <div class="side-band__accent side-band__accent--blue"></div>
      <div class="side-band__accent side-band__accent--sky"></div>
      <div class="side-band__accent side-band__accent--light"></div>
      <div class="side-band__gap side-band__gap--1"></div>
      <div class="side-band__gap side-band__gap--2"></div>
      <div class="side-band__gap side-band__gap--3"></div>
      <div class="side-band__gap side-band__gap--4"></div>
    </div>
    <span class="web-address">www.lorenzkeller.de</span>

    <div class="brand">
      <div class="brand__dot"></div>
      <div class="brand__name">Lorenz<br>Keller</div>
    </div>
    <div class="brand__divider"></div>

    <address class="contact">
      <div>Brunnerweg 14</div>
      <div>37281 Eichenfeld</div>
      <div>Germany</div>
      <div class="contact__row">
        <svg viewBox="0 0 10 10"><path d="M2 0l2 2-1 1.5c.8 1.6 1.9 2.7 3.5 3.5L8 6l2 2-1.5 2C4 9.5.5 6 0 1.5z"/></svg>
        <span>0871 294 55</span>
      </div>
      <div class="contact__row">
        <svg viewBox="0 0 10 10"><rect x="0" y="3" width="10" height="6" rx="1"/><rect x="2" y="0" width="6" height="3"/></svg>
        <span>0871 294 56</span>
      </div>
      <div class="contact__row">
        <svg viewBox="0 0 10 10"><path d="M0 2h10v6H0z"/><path d="M0 2l5 3.5L10 2" fill="none" stroke="#fff" stroke-width="1"/></svg>
        <span>info@lorenzkeller.de</span>
      </div>
    </address>

    <p class="sender-line">Lorenz Keller · Brunnerweg 14 · 37281 Eichenfeld · Germany</p>
  </article>
</div>
</body>
</html>
```